Brivo Hair

Hello - our company Vantor 4 develops novel products for the skin, & hair care industry as well as dietary supplements. We're looking for a label design for a new product. The product is a premium hair loss/growth supplement. Our primary demo is women ages 45-65. I attached the brand logo & some competitive product designs that we find attractive.

I've been traveling & have not had the time to adequately review the designs, please be patient with me.

```html
<!DOCTYPE html>
<html lang="en">
<head>
<meta charset="utf-8">
<title>Brivo Hair – Advanced Hair Regrowth Shot Label</title>
<link rel="stylesheet" href="https://fonts.googleapis.com/css2?family=Cinzel:wght@700&family=Exo+2:wght@400;600;700&family=Montserrat:wght@600;700&family=Tinos:wght@700&display=swap">
<style>
  :root {
    --stage: #4d4d4d;
    --stage-light: #7a7a7a;
    --label-black: #000000;
    --blue-deep: #0b4db3;
    --blue-mid: #1c83dc;
    --blue-bright: #2fb2fb;
    --logo-blue: #5cb6ea;
    --hair-grey: #a9b7c6;
    --silver-light: #f2f2f2;
    --silver-dark: #a8a8a8;
    --white: #ffffff;
    --ink: #111111;
    --tick-blue: #2a9be8;
  }
  * { margin: 0; padding: 0; box-sizing: border-box; }
  html, body { width: 692px; height: 1200px; overflow: hidden; }
  body {
    background: linear-gradient(110deg, var(--stage) 0%, var(--stage-light) 100%);
    position: relative;
  }
  .label {
    position: absolute;
    left: 26px; top: 185px;
    width: 640px; height: 830px;
    background: var(--label-black);
    overflow: hidden;
    box-shadow: 0 10px 30px rgba(0,0,0,.45);
  }
  .label__shapes { position: absolute; inset: 0; }
  .label__text { position: absolute; left: 0; width: 100%; text-align: center; white-space: nowrap; }

  .brand-name {
    top: 52px;
    font: 700 44px/1 "Montserrat", sans-serif;
    color: var(--white);
    letter-spacing: -1px;
  }
  .brand-tagline {
    top: 134px;
    font: 700 19px/1 "Montserrat", sans-serif;
    color: var(--white);
    letter-spacing: 1.5px;
  }
  .extract-box {
    position: absolute;
    left: 128px; top: 238px; width: 384px; height: 38px;
    border: 2px solid var(--blue-deep);
    border-radius: 3px;
    color: var(--white);
    font: 700 19px/34px "Cinzel", serif;
    letter-spacing: 2.5px;
    text-align: center;
  }
  .product-name {
    top: 290px;
    font: 700 86px/1 "Exo 2", sans-serif;
    color: var(--logo-blue);
    letter-spacing: 1px;
  }
  .strength {
    top: 414px;
    font: 700 30px/40px "Cinzel", serif;
    color: var(--ink);
    letter-spacing: 5px;
  }
  .advanced {
    top: 474px;
    font: 700 64px/1 "Tinos", serif;
    color: var(--white);
    letter-spacing: -1px;
  }
  .subtitle {
    top: 542px;
    font: 700 32px/1 "Tinos", serif;
    color: var(--white);
  }
  .illustration { position: absolute; border-radius: 50%; }
  .illustration--herbs {
    left: 173px; top: 615px; width: 118px; height: 126px;
    border-radius: 40% 40% 50% 50%;
    background: radial-gradient(circle at 50% 60%, #3aa43c 0%, #2a7d2e 55%, rgba(0,0,0,0) 75%);
  }
  .illustration--follicle {
    left: 395px; top: 606px; width: 122px; height: 100px;
    background: radial-gradient(circle, #3a4350 0%, #1a1f26 55%, rgba(0,0,0,0) 72%);
  }
  .benefits {
    position: absolute; left: 300px; top: 692px;
    list-style: none;
    font: 400 21px/1 "Exo 2", sans-serif;
    color: var(--white);
  }
  .benefits li { display: flex; align-items: center; gap: 6px; margin-bottom: 13px; }
  .benefits svg { width: 16px; height: 16px; flex: none; }
  .count-badge {
    position: absolute; left: 75px; top: 713px; width: 94px; height: 117px;
    border-radius: 47px 47px 0 0;
    background: linear-gradient(90deg, var(--silver-dark), var(--silver-light) 50%, var(--silver-dark));
    text-align: center;
  }
  .count-badge__number {
    display: block; margin-top: 26px;
    font: 700 52px/1 "Exo 2", sans-serif;
    color: var(--ink);
  }
  .count-badge__unit {
    display: block; margin-top: 6px; height: 24px;
    background: var(--blue-deep);
    font: 700 16px/24px "Exo 2", sans-serif;
    color: var(--white);
  }
  .format-line {
    top: 786px; left: 170px; width: 470px;
    font: 700 26px/1 "Exo 2", sans-serif;
    color: var(--white);
    letter-spacing: 2px;
  }
</style>
</head>
<body>
  <main class="label">
    <svg class="label__shapes" viewBox="0 0 640 830" aria-hidden="true">
      <defs>
        <linearGradient id="blueBand" x1="0" x2="1" y1="0" y2="0">
          <stop offset="0" stop-color="var(--blue-mid)"/>
          <stop offset="0.45" stop-color="var(--blue-bright)"/>
          <stop offset="1" stop-color="var(--blue-deep)"/>
        </linearGradient>
        <linearGradient id="silver" x1="0" x2="1" y1="0" y2="0">
          <stop offset="0" stop-color="var(--silver-dark)"/>
          <stop offset="0.5" stop-color="var(--silver-light)"/>
          <stop offset="1" stop-color="var(--silver-dark)"/>
        </linearGradient>
      </defs>
      <!-- header shield with silver edge -->
      <polygon class="header-edge" fill="url(#silver)"
        points="0,134 110,134 135,174 320,219 505,174 530,134 640,134 640,142 533,142 510,182 320,226 130,182 107,142 0,142"/>
      <polygon class="header-shield" fill="url(#blueBand)"
        points="0,0 640,0 640,134 530,134 505,174 320,206 135,174 110,134 0,134"/>
      <!-- strength band -->
      <rect class="strength-band" x="0" y="409" width="640" height="50" fill="url(#silver)"/>
      <!-- title band -->
      <polygon class="title-band" fill="url(#blueBand)"
        points="0,460 640,460 640,541 588,541 531,598 108,598 70,541 0,541"/>
      <!-- footer band -->
      <rect class="footer-band" x="0" y="778" width="640" height="52" fill="url(#blueBand)"/>
    </svg>

    <p class="label__text brand-name">VANTOR 4</p>
    <p class="label__text brand-tagline">MEDICALLY PROVEN</p>

    <p class="extract-box">HE SHOU WU 12:1 EXTRACT</p>
    <h1 class="label__text product-name">BRIVO HAIR</h1>
    <p class="label__text strength">CLINICAL STRENGTH</p>
    <p class="label__text advanced">ADVANCED</p>
    <p class="label__text subtitle">HAIR REGROWTH SHOT</p>

    <div class="illustration illustration--herbs" role="img" aria-label="Green herbal mortar and pestle with leaves"></div>
    <div class="illustration illustration--follicle" role="img" aria-label="Hair follicle cross-section in a blue circle"></div>

    <ul class="benefits">
      <li><svg viewBox="0 0 16 16"><circle cx="8" cy="8" r="6.8" fill="none" stroke="var(--tick-blue)" stroke-width="1.4"/><path d="M4.8 8.2l2.2 2.2 4.2-4.4" fill="none" stroke="var(--tick-blue)" stroke-width="1.5"/></svg>Biotin</li>
      <li><svg viewBox="0 0 16 16"><circle cx="8" cy="8" r="6.8" fill="none" stroke="var(--tick-blue)" stroke-width="1.4"/><path d="M4.8 8.2l2.2 2.2 4.2-4.4" fill="none" stroke="var(--tick-blue)" stroke-width="1.5"/></svg>Collagen 30,000 mcg</li>
    </ul>

    <div class="count-badge">
      <span class="count-badge__number">60</span>
      <span class="count-badge__unit">CAPSULES</span>
    </div>
    <p class="label__text format-line">HAIR GROWTH LIQUID DROPS</p>
  </main>
</body>
</html>
```